Clean business card with logo provided

I want a card that will stand out among the masses. I need the color and image to show professionalism and yet have a family appeal showing that I only deal with win/win scenarios. The back of the card will be used to take notes about the individual so I can use that in my database entry. I like modern design but need professionalism in it also. It needs to fit my "clean, safe, and affordable housing" motto. I need to be able to write on the file and update the card details for my employees.

Target Market(s)

Investors looking to make investment income through real estate

Industry/Entity Type

Real Estate

Contact Information for Business Card

Brent Kovalich
blank address, city, st, zip code
480-555-3174
brentkovalich@ridgeworthrentals.example
www.ridgeworthrentals.example

Font styles to use
Sans Serif

Requirements
Must have
• I would like the back of the card to have lines for info. example
• Met/Visited: Date:
• Interets:
Nice to have
• I want the cards color to match the logo background color. Font with details to be san serif and black. I want the card rectangular with square corners. Standard business card size. I would like to see cards designed with both images to see which i prefer more.

```html
<!DOCTYPE html>
<html lang="en">
<head>
<meta charset="utf-8">
<title>Ridgeworth Rentals – Business Card</title>
<link rel="stylesheet" href="https://fonts.googleapis.com/css2?family=Cinzel:wght@400;500&family=Open+Sans:wght@400;600&display=swap">
<style>
  :root {
    --backdrop: #8e8f91;
    --card-black: #000000;
    --note-paper: #e8e9eb;
    --teal: #1b9fb3;
    --text-light: #d9d9d9;
    --line-ink: #1a1a1a;
  }
  * { margin: 0; padding: 0; box-sizing: border-box; }
  html, body {
    width: 1105px;
    height: 1200px;
    overflow: hidden;
    background: var(--backdrop);
    font-family: "Open Sans", Arial, sans-serif;
  }
  .card {
    position: absolute;
    left: 182px;
    width: 746px;
    height: 426px;
    overflow: hidden;
  }
  .card-front { top: 119px; background: var(--card-black); text-align: center; }
  .card-back { top: 636px; background: var(--note-paper); }

  /* Front */
  .brand-mark {
    position: absolute;
    top: 110px;
    left: 0; right: 0;
    display: flex;
    justify-content: center;
    align-items: center;
    gap: 12px;
    color: #e6e6e6;
    font-size: 24px;
    letter-spacing: 1px;
  }
  .brand-mark .dot {
    width: 14px; height: 14px;
    border-radius: 50%;
    background: #e6e6e6;
  }
  .holder-name {
    position: absolute;
    top: 198px; left: 0; right: 0;
    font-family: "Cinzel", Georgia, serif;
    font-size: 28px;
    color: var(--teal);
    letter-spacing: 0.5px;
  }
  .contact-line {
    position: absolute;
    left: 0; right: 0;
    color: var(--text-light);
    white-space: nowrap;
  }
  .contact-email { top: 238px; font-size: 19px; }
  .contact-address { top: 272px; font-size: 21px; }
  .contact-links { top: 306px; font-size: 21px; }
  .contact-links .label { color: var(--teal); }

  /* Back */
  .back-band {
    position: absolute;
    top: 0; left: 0;
    width: 100%; height: 179px;
    background: var(--card-black);
    text-align: center;
  }
  .back-brand {
    position: absolute;
    top: 42px; left: 0; right: 0;
    display: flex;
    justify-content: center;
    align-items: center;
    gap: 16px;
    color: var(--teal);
    font-size: 40px;
    letter-spacing: 2px;
  }
  .back-brand .dot {
    width: 26px; height: 26px;
    border-radius: 50%;
    background: var(--teal);
  }
  .tagline {
    position: absolute;
    top: 124px; left: 0; right: 0;
    color: var(--teal);
    font-size: 12px;
    font-weight: 600;
    letter-spacing: 0.6px;
  }
  .note-row {
    position: absolute;
    left: 55px;
    width: 624px;
    display: flex;
    align-items: flex-end;
    font-size: 19px;
    color: var(--teal);
    line-height: 1;
  }
  .note-row .write-line {
    flex: 1;
    border-bottom: 1.5px solid var(--line-ink);
    margin-left: 4px;
    margin-bottom: 2px;
  }
  .row-met { top: 220px; }
  .row-date { top: 271px; }
  .row-interests { top: 322px; }
  .row-extra { top: 360px; height: 22px; }
  .row-extra .write-line { margin-left: 0; }
</style>
</head>
<body>
  <section class="card card-front">
    <div class="brand-mark"><span class="dot"></span><span>Ridgeworth Rentals</span></div>
    <h1 class="holder-name">BRENT KOVALICH</h1>
    <p class="contact-line contact-email">brentkovalich@ridgeworthrentals.example</p>
    <p class="contact-line contact-address">4120 Larkspur Court, Fairbanks, Alaska 99701</p>
    <p class="contact-line contact-links"><span class="label">Phone :</span> 480-555-3174 &nbsp;<span class="label">Web :</span> ridgeworthrentals.example</p>
  </section>

  <section class="card card-back">
    <div class="back-band">
      <div class="back-brand"><span>Ridgeworth Rentals LLC</span><span class="dot"></span></div>
      <p class="tagline">Providing clean, safe, and affordable housing</p>
    </div>
    <div class="note-row row-met"><span>MET/VISITED:</span><span class="write-line"></span></div>
    <div class="note-row row-date"><span>DATE:</span><span class="write-line"></span></div>
    <div class="note-row row-interests"><span>INTERESTS:</span><span class="write-line"></span></div>
    <div class="note-row row-extra"><span class="write-line"></span></div>
  </section>
</body>
</html>
```